Northfield Builders Guild Business card

We are looking for a new business card design with photo included.
Our business is a nonprofit construction contractor membership organization. We offer business education, assist with business setup and licensing, provide safety training, and provide a member directory.
URL: www.builderslinkguild.org
Color code:
CMYK: 0 cyan, 42 magenta, 100 yellow, 0 black for Print.
Hexidecimal: #FF9900
RGB: R 255; G 153; B 0

```html
<!DOCTYPE html>
<html lang="en">
<head>
<meta charset="utf-8">
<title>Northfield Builders Guild – Business Card</title>
<link href="https://fonts.googleapis.com/css2?family=Montserrat:wght@400;500;700;800&display=swap" rel="stylesheet">
<style>
  :root {
    --orange: #ff9900;
    --ink: #2e2e2e;
    --grey: #555555;
    --rule: #9a9a9a;
    --paper: #ffffff;
    --backdrop: #e9e9e9;
    --card-dark: #2b2b2b;
  }
  * { box-sizing: border-box; margin: 0; padding: 0; }
  html, body {
    width: 1200px; height: 866px; overflow: hidden;
    background: var(--backdrop);
    font-family: "Montserrat", Arial, sans-serif;
  }
  .sheet {
    width: 1200px; height: 866px;
    display: flex; flex-direction: column; align-items: center; justify-content: center;
    gap: 30px;
  }
  .card {
    position: relative;
    width: 680px; height: 389px;
    box-shadow: 0 6px 18px rgba(0,0,0,0.18);
    overflow: hidden;
  }
  .card--front { background: var(--paper); }

  .contact { position: absolute; left: 44px; top: 48px; }
  .contact__name {
    color: var(--orange); font-weight: 700; font-size: 24px;
    letter-spacing: 0.5px; text-transform: uppercase;
  }
  .contact__title {
    color: var(--grey); font-size: 13px; letter-spacing: 1px;
    text-transform: uppercase; margin-top: 2px;
  }
  .contact__list { list-style: none; margin-top: 16px; }
  .contact__item {
    display: flex; align-items: center; gap: 9px;
    color: var(--ink); font-size: 15px; line-height: 25px;
  }
  .contact__icon { width: 18px; height: 18px; flex: none; }

  .brand {
    position: absolute; right: 44px; top: 52px; width: 290px;
    color: var(--ink); font-weight: 800; font-size: 34px; line-height: 1.05;
    text-transform: uppercase; text-align: right;
  }

  .divider {
    position: absolute; left: 300px; right: 44px; top: 236px;
    height: 1px; background: var(--rule);
  }

  .address {
    position: absolute; right: 44px; bottom: 40px;
    text-align: right; color: var(--ink); font-size: 16px; line-height: 22px;
  }

  .card--back { background: var(--card-dark); }
  .back__pattern {
    position: absolute; inset: 0;
    background: radial-gradient(circle at 30% 40%, #363636 0%, var(--card-dark) 60%);
  }
  .back__brand {
    position: absolute; inset: 0;
    display: flex; align-items: center; justify-content: center; gap: 18px;
  }
  .back__dot { width: 54px; height: 54px; border-radius: 50%; background: var(--orange); }
  .back__name {
    color: var(--paper); font-weight: 800; font-size: 30px;
    text-transform: uppercase; letter-spacing: 0.5px;
  }
</style>
</head>
<body>
<main class="sheet">
  <section class="card card--front" aria-label="Business card front">
    <div class="contact">
      <p class="contact__name">Daniel Reeves</p>
      <p class="contact__title">Managing Director</p>
      <ul class="contact__list">
        <li class="contact__item">
          <svg class="contact__icon" viewBox="0 0 18 18" aria-hidden="true"><circle cx="9" cy="9" r="9" fill="var(--orange)"/><path d="M5.5 5c.6-.6 1.4-.5 1.7.1l.7 1.4c.2.4 0 .8-.3 1l-.6.4c.5 1 1.3 1.8 2.2 2.3l.4-.6c.2-.3.7-.5 1-.3l1.4.7c.6.3.7 1.1.1 1.7-1 1-2.6.8-4.3-.8C6.2 9.2 4.5 6.7 5.5 5z" fill="#fff"/></svg>
          (541) 555-0142 (Office)
        </li>
        <li class="contact__item">
          <svg class="contact__icon" viewBox="0 0 18 18" aria-hidden="true"><circle cx="9" cy="9" r="9" fill="var(--orange)"/><rect x="6" y="4" width="6" height="10" rx="1" fill="none" stroke="#fff" stroke-width="1.3"/><circle cx="9" cy="12" r="0.7" fill="#fff"/></svg>
          800-555-0176
        </li>
        <li class="contact__item">
          <svg class="contact__icon" viewBox="0 0 18 18" aria-hidden="true"><circle cx="9" cy="9" r="9" fill="var(--orange)"/><rect x="6" y="4" width="6" height="3" fill="#fff"/><rect x="4.5" y="7.5" width="9" height="4.5" rx="1" fill="#fff"/><rect x="6" y="11" width="6" height="3" fill="#fff" stroke="var(--orange)" stroke-width="0.6"/></svg>
          503.555.0193
        </li>
        <li class="contact__item">
          <svg class="contact__icon" viewBox="0 0 18 18" aria-hidden="true"><circle cx="9" cy="9" r="9" fill="var(--orange)"/><rect x="4.5" y="5.5" width="9" height="7" fill="#fff"/><path d="M4.5 5.5 9 9.5l4.5-4" fill="none" stroke="var(--orange)" stroke-width="1"/></svg>
          support@nbguild.org
        </li>
        <li class="contact__item">
          <svg class="contact__icon" viewBox="0 0 18 18" aria-hidden="true"><circle cx="9" cy="9" r="9" fill="var(--orange)"/><g fill="none" stroke="#fff" stroke-width="1"><circle cx="9" cy="9" r="4.5"/><ellipse cx="9" cy="9" rx="2" ry="4.5"/><path d="M4.5 9h9"/></g></svg>
          www.builderslinkguild.org
        </li>
      </ul>
    </div>

    <p class="brand">Northfield Builders Guild</p>

    <div class="divider"></div>

    <address class="address" style="font-style:normal">
      2450 NW Cedar Lane<br>
      Suite #100, Salem<br>
      OR 97301
    </address>
  </section>

  <section class="card card--back" aria-label="Business card back">
    <div class="back__pattern" role="img" aria-label="Dark background with faint overlapping ring pattern"></div>
    <div class="back__brand">
      <span class="back__dot"></span>
      <span class="back__name">Northfield Builders Guild</span>
    </div>
  </section>
</main>
</body>
</html>
```